Website Design Request - Management Consulting Firm

We need a Website designed for an IT Management Staffing and Recruiting firm called TRAVENOK based in San Francisco.

The firm is an high-end technology staffing agency. Our focus is on quality and high-caliber candidates rather than quantity.

The website will have two main home pages. One for the recruiter and another on for the candidates.

The website needs to optimize for mobile devices as well.

I have attached few mock-ups that I have done just to show what I am thinking. The UI needs to be very clean, fluid, and it needs to have a modern, rustic, professional feel to it.

Target Market(s)

Technology Manager, Director, VP, CIO of Companies that have $4b-10b dollar revenue. Such as larkspurdwellings.example , https://www.velmorian.example/, quillnet.example, zib.example

Industry/Entity Type

Management Consulting

Number of Pages Required

5+ page

Font styles to use
Sans Serif

Colors
f37122
ffffff

Requirements
Must have
• Please review mock-ups for suggestions
Nice to have
Should not have

```html
<!DOCTYPE html>
<html lang="en">
<head>
<meta charset="utf-8">
<title>TRAVENOK – IT Project Management Jobs</title>
<link rel="stylesheet" href="https://fonts.googleapis.com/css2?family=Nunito+Sans:wght@300;400;600&display=swap">
<style>
  :root {
    --orange: #f37122;
    --orange-deep: #ee5f12;
    --white: #ffffff;
    --ink: #333333;
    --ink-soft: #666666;
    --muted: #a9a9a9;
    --line: #d9d9d9;
    --band: #e9e9e9;
    --footer: #f2f2f2;
    --number: #dedede;
  }
  * { box-sizing: border-box; margin: 0; padding: 0; }
  html, body { width: 839px; height: 1200px; overflow: hidden; background: var(--white); }
  body { position: relative; font-family: "Nunito Sans", sans-serif; color: var(--ink); }
  .abs { position: absolute; }

  /* Header */
  .site-header { position: absolute; left: 0; top: 0; width: 839px; height: 64px; background: var(--white); }
  .brand { position: absolute; left: 99px; top: 16px; font-size: 27px; font-weight: 600; letter-spacing: 1px; color: var(--orange); line-height: 32px; }
  .main-nav a { position: absolute; top: 25px; font-size: 12.5px; color: var(--ink); text-decoration: none; line-height: 16px; }

  /* Hero */
  .hero { position: absolute; left: 0; top: 64px; width: 839px; height: 338px; }
  .hero-photo { position: absolute; inset: 0; background: radial-gradient(ellipse at 75% 40%, #9a9a9a 0%, #7e7e7e 45%, #666 100%), linear-gradient(120deg, #5c5c5c, #8c8c8c); }
  .hero-title { position: absolute; left: 0; width: 839px; top: 88px; text-align: center; color: var(--white); font-size: 28px; font-weight: 400; line-height: 36px; }
  .hero-sub { position: absolute; left: 0; width: 839px; top: 124px; text-align: center; color: var(--white); font-size: 17px; font-weight: 300; line-height: 22px; }
  .email-field { position: absolute; left: 245px; top: 160px; width: 337px; height: 31px; background: var(--white); border: none; font-family: inherit; font-size: 9.5px; color: var(--muted); padding-left: 15px; line-height: 31px; }
  .btn-offers { position: absolute; left: 315px; top: 199px; width: 202px; height: 29px; background: linear-gradient(var(--orange), var(--orange-deep)); color: var(--white); font-size: 12.5px; text-align: center; line-height: 29px; }
  .hero-note { position: absolute; left: 0; width: 839px; top: 241px; text-align: center; color: var(--white); font-size: 9.5px; line-height: 14px; }
  .hero-note span { text-decoration: underline; }
  .carousel-dots { position: absolute; top: 313px; left: 391px; display: flex; gap: 6px; }
  .carousel-dots i { width: 9px; height: 9px; border-radius: 50%; background: var(--white); border: 1px solid var(--white); display: block; }
  .carousel-dots i.current { background: transparent; }

  /* Tabs */
  .tab-band { position: absolute; left: 0; top: 402px; width: 839px; height: 35px; background: var(--band); }
  .tab { position: absolute; top: 0; height: 35px; line-height: 35px; font-size: 16px; text-align: center; }
  .tab-active { left: 260px; width: 162px; background: var(--orange); color: var(--white); }
  .tab-active::after { content: ""; position: absolute; left: 74px; top: 35px; border: 7px solid transparent; border-top-color: var(--orange); }
  .tab-idle { left: 440px; width: 100px; color: var(--muted); }

  /* Steps */
  .steps-title { position: absolute; left: 0; width: 839px; top: 479px; text-align: center; font-size: 13px; line-height: 18px; }
  .steps-lead { position: absolute; left: 0; width: 839px; top: 505px; text-align: center; font-size: 14px; font-weight: 300; color: var(--muted); line-height: 18px; }
  .step-frame { position: absolute; left: 0; top: 0; }
  .step-num { position: absolute; font-size: 42px; font-weight: 300; color: var(--number); line-height: 48px; }
  .step-title { position: absolute; left: 300px; font-size: 18.5px; font-weight: 300; line-height: 24px; }
  .step-text { position: absolute; left: 301px; font-size: 11.5px; color: var(--ink-soft); line-height: 17px; font-weight: 300; }
  .btn-upload { position: absolute; left: 322px; top: 907px; width: 169px; height: 37px; border: 1.5px solid var(--orange); border-radius: 19px; color: var(--orange); font-size: 13px; text-align: center; line-height: 34px; }

  /* Footer */
  .site-footer { position: absolute; left: 0; top: 996px; width: 839px; height: 204px; background: var(--footer); }
  .footer-col { position: absolute; top: 32px; }
  .footer-col h3 { font-size: 15px; font-weight: 300; color: #777; line-height: 20px; margin-bottom: 5px; }
  .footer-col li { list-style: none; font-size: 8.5px; color: #888; line-height: 16.3px; padding-left: 2px; }
  .social { display: flex; gap: 7px; margin-top: 3px; }
  .social i { width: 24px; height: 24px; border-radius: 50%; background: var(--orange); display: block; }
  .footer-brand { margin-top: 14px; font-size: 34px; font-weight: 600; color: #cfcfcf; letter-spacing: 1px; line-height: 40px; }
  .copyright { position: absolute; left: 122px; top: 164px; font-size: 8.5px; color: #888; }
</style>
</head>
<body>

<header class="site-header">
  <div class="brand">TRAVENOK</div>
  <nav class="main-nav">
    <a style="left:437px">Professionals</a>
    <a style="left:538px">Employers</a>
    <a style="left:626px">Sign In</a>
    <a style="left:694px">Sign Up</a>
  </nav>
</header>

<section class="hero">
  <div class="hero-photo" role="img" aria-label="Desk photo with laptop keyboard, glasses, pen and a cup of coffee"></div>
  <h1 class="hero-title">Looking for IT Project Management Jobs?</h1>
  <p class="hero-sub">Upload your resume, accept interview requests, get offer.</p>
  <div class="email-field">Your Email address</div>
  <div class="btn-offers">Get Offers Now</div>
  <p class="hero-note">Looking for talents? <span>See how it works for Employers</span></p>
  <div class="carousel-dots"><i class="current"></i><i></i><i></i><i></i></div>
</section>

<div class="tab-band">
  <div class="tab tab-active">How it Works</div>
  <div class="tab tab-idle">Why Us?</div>
</div>

<h2 class="steps-title" style="font-weight:400">3 Simple Steps</h2>
<p class="steps-lead">Employers pay 25% more for a better FIT Project Manager</p>

<svg class="step-frame" width="839" height="1200" viewBox="0 0 839 1200" fill="none">
  <path d="M678,547 H180 A53.5,53.5 0 0 0 180,654 H672 A53.5,53.5 0 0 1 672,761 H180 A53.5,53.5 0 0 0 180,868 H674" stroke="var(--line)" stroke-width="1.2"/>
  <!-- upload cloud -->
  <g stroke="var(--orange)" stroke-width="2" stroke-linecap="round" stroke-linejoin="round">
    <path d="M168,618 C152,618 148,598 162,592 C160,578 176,570 186,578 C192,562 216,564 216,582 C230,582 230,608 216,610"/>
    <circle cx="187" cy="616" r="15"/>
    <path d="M187,624 V608 M181,614 L187,608 L193,614"/>
    <!-- envelope -->
    <rect x="614" y="683" width="59" height="42" rx="2"/>
    <path d="M614,685 L643,708 L673,685 M614,724 L636,703 M673,724 L651,703"/>
    <!-- bonus hand -->
    <circle cx="191" cy="802" r="10"/>
    <path d="M181,784 v-6 M191,783 v-8 M201,784 v-6"/>
    <path d="M164,822 C176,818 184,820 192,826 L210,826 M164,822 L184,836 L214,838 M214,820 V842 M214,822 H226 M214,840 H230"/>
  </g>
  <text x="191" y="807" text-anchor="middle" font-family="Nunito Sans, sans-serif" font-size="13" font-weight="600" fill="var(--orange)">$</text>
</svg>

<div class="step-num" style="left:262px;top:570px">1</div>
<h3 class="step-title" style="top:578px">Upload your Resume</h3>
<p class="step-text" style="left:302px;top:605px">Answer few questions and upload your resume</p>

<div class="step-num" style="left:263px;top:677px">2</div>
<h3 class="step-title" style="left:301px;top:677px">We Send You Interview Requests</h3>
<p class="step-text" style="top:703px">Interested in someone? With a single clic,<br>send interview request and let us handle the rest</p>

<div class="step-num" style="left:263px;top:792px">3</div>
<h3 class="step-title" style="left:301px;top:795px">Get $1000 Bonus</h3>
<p class="step-text" style="top:822px">Find a Job and get $1000 bonus TRAVENOK</p>

<div class="btn-upload">Upload Your Resume</div>

<footer class="site-footer">
  <div class="footer-col" style="left:122px">
    <h3>Company</h3>
    <ul><li>Home</li><li>Why We Are</li><li>About Us</li><li>Our Team</li></ul>
  </div>
  <div class="footer-col" style="left:248px">
    <h3>Sublinks</h3>
    <ul><li>How it works</li><li>Emloyers</li><li>Professionals</li><li>Join Us</li></ul>
  </div>
  <div class="footer-col" style="left:380px">
    <h3>Resources</h3>
    <ul><li>Term of Use</li><li>Support</li><li>Privacy Policy</li><li>Contact Us</li></ul>
  </div>
  <div class="footer-col" style="left:515px">
    <h3>Follow Us</h3>
    <div class="social"><i></i><i></i><i></i><i></i></div>
    <div class="footer-brand">TRAVENOK</div>
  </div>
  <p class="copyright">© 2016 Company Name&nbsp; All right reserved</p>
</footer>

</body>
</html>
```